CONTEMPORARY Canva Art Design for Christians

I need a canvas art design on Christianity. The design must be in 3 SIMPLE dimensions: 12x 18 inches / 28 x 24 inches / 30 x 40 inches
The design must be accompanied by christian quote.
The christian quote can be "As For Me And My House We Will Serve The Lord (Joshua 24:15)" or any other quote that is good for display in a christian home.

I DON'T WANT THE TRADITIONAL CHRISTIAN DESIGN.. I WANT COLOURFUL, MEANINGFUL and CONTEMPORARY, MODERN DESIGN. And stay away from the scary image of Jesus in dark background, it only makes the home more scary not holy!

Target Market(s)

Christians

Colors

Designer to choose colors to be used in the design.

Requirements
Must have
• A graphic design and a christian quote that is powerful and edifies the soul. Great for display at home. Great use of colours to enhance the message.
Nice to have
• I wish to see great unique design with strong use of colours, images to enhance the scripture. It must glorify Jesus.
Should not have
• Should not be dull.

```html
<!DOCTYPE html>
<html lang="en">
<head>
<meta charset="utf-8">
<title>As For Me And My House — Canvas Art</title>
<link href="https://fonts.googleapis.com/css2?family=Roboto+Condensed:wght@700&family=Crimson+Text:wght@400&display=swap" rel="stylesheet">
<style>
  :root {
    --page: #eef1f4;
    --ink-white: #ffffff;
    --shadow: rgba(40, 20, 0, 0.8);
    --red: #d8261c;
    --orange: #f08a12;
    --amber: #f7b51a;
    --yellow: #fbe23a;
    --lime: #8cc43a;
    --rust: #b5451a;
    --magenta: #c2185b;
    --sky: #4a86b8;
    --wheat: #c98a2c;
    --wheat-dark: #7a4a16;
    --robe: #e9dcc0;
    --cross: #6b2a10;
  }
  html, body {
    margin: 0;
    padding: 0;
    width: 1200px;
    height: 877px;
    overflow: hidden;
    background: var(--page);
  }
  .canvas-art {
    position: absolute;
    left: 30px;
    top: 60px;
    width: 1140px;
    height: 756px;
    overflow: hidden;
    box-shadow: 0 6px 18px rgba(0,0,0,0.25);
    background:
      radial-gradient(ellipse 40% 45% at 62% 30%, var(--yellow) 0%, transparent 70%),
      radial-gradient(ellipse 35% 40% at 22% 28%, var(--lime) 0%, transparent 70%),
      radial-gradient(ellipse 30% 30% at 95% 8%, var(--magenta) 0%, transparent 70%),
      radial-gradient(ellipse 45% 35% at 80% 85%, var(--rust) 0%, transparent 75%),
      linear-gradient(135deg, var(--red) 0%, var(--orange) 30%, var(--amber) 55%, var(--orange) 80%, var(--rust) 100%);
  }
  .abstract-backdrop {
    position: absolute;
    inset: 0;
  }
  .sunset-field {
    position: absolute;
    left: 0;
    top: 410px;
    width: 540px;
    height: 346px;
    background:
      linear-gradient(180deg, var(--sky) 0%, var(--amber) 22%, var(--wheat) 35%, var(--wheat-dark) 100%);
    -webkit-mask-image: linear-gradient(90deg, #000 70%, transparent 100%);
    mask-image: linear-gradient(90deg, #000 70%, transparent 100%);
  }
  .shepherd-figure {
    position: absolute;
    left: 82px;
    top: 516px;
    width: 186px;
    height: 240px;
    background: linear-gradient(180deg, var(--wheat-dark) 0%, var(--robe) 35%, #d9c7a0 100%);
    border-radius: 90px 90px 0 0;
    opacity: 0.85;
  }
  .cross {
    position: absolute;
    left: 905px;
    top: 81px;
  }
  .quote {
    position: absolute;
    margin: 0;
    font-family: "Roboto Condensed", "Arial Narrow", sans-serif;
    font-weight: 700;
    color: var(--ink-white);
    line-height: 1;
    letter-spacing: -1px;
    text-shadow: 5px 5px 0 var(--shadow), 0 0 10px rgba(0,0,0,0.25);
    white-space: nowrap;
  }
  .quote small { font-size: 0.72em; }
  .line-1 { left: 154px; top: 83px;  font-size: 137px; }
  .line-2 { left: 257px; top: 215px; font-size: 137px; }
  .line-3 { left: 158px; top: 338px; font-size: 139px; }
  .line-4 { left: 393px; top: 456px; font-size: 182px; letter-spacing: -2px; }
  .reference {
    position: absolute;
    left: 712px;
    top: 622px;
    margin: 0;
    font-family: "Crimson Text", Georgia, serif;
    font-size: 58px;
    line-height: 1;
    font-variant: small-caps;
    color: var(--ink-white);
    letter-spacing: 1px;
    white-space: nowrap;
  }
</style>
</head>
<body>
  <main class="canvas-art">
    <div class="abstract-backdrop" role="img" aria-label="Colourful abstract polygon burst in red, orange, yellow and green with glowing light sparks"></div>
    <div class="sunset-field" role="img" aria-label="Golden wheat field at sunset under a blue sky"></div>
    <div class="shepherd-figure" role="img" aria-label="Robed shepherd figure cradling a lamb, standing in the wheat field"></div>
    <svg class="cross" width="66" height="66" viewBox="0 0 66 66" aria-hidden="true">
      <rect x="29" y="0" width="8" height="66" fill="var(--cross)"/>
      <rect x="10" y="15" width="46" height="8" fill="var(--cross)"/>
    </svg>
    <h1 class="quote line-1">As For Me</h1>
    <p class="quote line-2"><small>And</small> My House</p>
    <p class="quote line-3"><small>We</small> Will Serve</p>
    <p class="quote line-4">The LORD.</p>
    <p class="reference">(Joshua 24:15)</p>
  </main>
</body>
</html>
```